Dunmore Roofing

Want a professional looking business card

Industry/Entity Type

Business

Contact Information for Business Card

Paul Dunmore ( Owner) paul@dunmoreroofing-example.com, www.dunmoreroofing-example.com, Adress: 4172 Township road 43 Millbrook Falls,ON K9X4T2

```html
<!DOCTYPE html>
<html lang="en">
<head>
<meta charset="utf-8">
<title>Dunmore Roofing – Business Cards</title>
<link rel="stylesheet" href="https://fonts.googleapis.com/css2?family=Source+Sans+3:wght@400;600;700&display=swap">
<style>
  :root {
    --backdrop: #8b8c8e;
    --brand-blue: #1d4289;
    --slate: #737477;
    --slate-back: #7a7b7d;
    --mist: #dcdddf;
    --stripe: #d5d6d8;
    --lavender: #c9cadf;
    --paper: #ffffff;
    --ink-grey: #5d5e61;
  }
  * { box-sizing: border-box; margin: 0; padding: 0; }
  html, body { width: 1200px; height: 828px; overflow: hidden; }
  body {
    background: var(--backdrop);
    font-family: "Source Sans 3", "Myriad Pro", sans-serif;
    position: relative;
  }
  .card {
    position: absolute;
    width: 547px;
    height: 313px;
    background: var(--paper);
    overflow: hidden;
  }
  .card--front-blue { left: 318px; top: 64px; }
  .card--front-grey { left: 43px; top: 426px; }
  .card--back { left: 614px; top: 426px; background: var(--slate-back); }
  .card__shapes { position: absolute; inset: 0; }
  .holder { position: absolute; left: 19px; top: 28px; color: var(--paper); }
  .holder__name { font-size: 23px; font-weight: 600; line-height: 1.1; }
  .holder__role { font-size: 16px; font-weight: 400; margin-top: 2px; }
  .contact {
    position: absolute; left: 19px; top: 184px;
    list-style: none; color: var(--paper); font-size: 14.5px; line-height: 21px;
  }
  .contact li { display: flex; align-items: center; gap: 6px; }
  .contact svg { width: 15px; height: 13px; fill: currentColor; flex: none; }
  .address { position: absolute; left: 19px; top: 282px; font-size: 13.5px; color: var(--paper); }
  .card--front-grey .address { color: var(--ink-grey); }
  .wordmark {
    position: absolute; left: 300px; top: 48px; width: 240px;
    text-align: center; color: var(--brand-blue);
    font-size: 30px; font-weight: 700; letter-spacing: 2px; line-height: 1.15;
    text-transform: uppercase;
  }
  .card--back .wordmark {
    left: 0; width: 547px; top: 102px; color: var(--paper);
    font-size: 38px; letter-spacing: 3px;
  }
  .back__texture {
    position: absolute; left: 90px; top: 30px; width: 380px; height: 210px;
    background: radial-gradient(ellipse at center, rgba(255,255,255,0.06), rgba(255,255,255,0) 70%);
  }
  .back__web {
    position: absolute; left: 0; width: 547px; top: 281px;
    text-align: center; color: var(--paper); font-size: 14px;
  }
</style>
</head>
<body>

<svg width="0" height="0" style="position:absolute" aria-hidden="true">
  <defs>
    <symbol id="icon-phone" viewBox="0 0 16 14"><path d="M2 3c0-1.5 3-2.5 6-2.5s6 1 6 2.5v1.5h-3V3.2C10 2.8 9 2.7 8 2.7s-2 .1-3 .5v1.3H2z"/><path d="M4 6h8l2 6.5H2z"/></symbol>
    <symbol id="icon-mail" viewBox="0 0 16 14"><rect x="1.2" y="2.2" width="13.6" height="9.6" fill="none" stroke="currentColor" stroke-width="1.6"/><path d="M1.5 2.8 8 8l6.5-5.2" fill="none" stroke="currentColor" stroke-width="1.6"/></symbol>
    <symbol id="icon-globe" viewBox="0 0 16 14"><path d="M8 .5a6.5 6.5 0 1 0 0 13 6.5 6.5 0 0 0 0-13zm0 1.2c.9 0 1.9 1.8 2.2 4.7H5.8C6.1 3.5 7.1 1.7 8 1.7zM2.8 6.4a5.3 5.3 0 0 1 2.4-3.9c-.4 1-.7 2.3-.8 3.9zm0 1.2h1.6c.1 1.6.4 2.9.8 3.9a5.3 5.3 0 0 1-2.4-3.9zM8 12.3c-.9 0-1.9-1.8-2.2-4.7h4.4c-.3 2.9-1.3 4.7-2.2 4.7zm2.8-.8c.4-1 .7-2.3.8-3.9h1.6a5.3 5.3 0 0 1-2.4 3.9zm.8-5.1c-.1-1.6-.4-2.9-.8-3.9a5.3 5.3 0 0 1 2.4 3.9z"/></symbol>
  </defs>
</svg>

<section class="card card--front-blue">
  <svg class="card__shapes" viewBox="0 0 547 313" aria-hidden="true">
    <polygon points="0,0 145,0 282,158 0,158" fill="var(--brand-blue)"/>
    <polygon points="153,0 171,0 352,205 342,313 324,313 334,205" fill="var(--stripe)"/>
    <polygon points="352,158 547,158 547,269 345,269 348,205" fill="var(--mist)"/>
    <polygon points="0,158 310,158 342,190 336,269 0,269" fill="var(--slate)"/>
    <polygon points="0,271 324,271 321,313 0,313" fill="var(--brand-blue)"/>
  </svg>
  <div class="holder">
    <p class="holder__name">Paul Dunmore</p>
    <p class="holder__role">Owner</p>
  </div>
  <ul class="contact">
    <li><svg><use href="#icon-phone"/></svg>(613) 555-0142</li>
    <li><svg><use href="#icon-mail"/></svg>paul@dunmoreroofing-example.com</li>
    <li><svg><use href="#icon-globe"/></svg>www.dunmoreroofing-example.com</li>
  </ul>
  <p class="address">4172 Township road 43, Millbrook Falls,ON K9X4T2</p>
  <p class="wordmark">Dunmore<br>Roofing</p>
</section>

<section class="card card--front-grey">
  <svg class="card__shapes" viewBox="0 0 547 313" aria-hidden="true">
    <polygon points="0,0 145,0 282,158 0,158" fill="var(--slate)"/>
    <polygon points="153,0 171,0 362,210 340,313 322,313 344,210" fill="var(--stripe)"/>
    <polygon points="312,158 547,158 547,269 354,269 360,210" fill="var(--lavender)"/>
    <polygon points="0,158 300,158 342,205 336,269 0,269" fill="var(--brand-blue)"/>
  </svg>
  <div class="holder">
    <p class="holder__name">Paul Dunmore</p>
    <p class="holder__role">Owner</p>
  </div>
  <ul class="contact">
    <li><svg><use href="#icon-phone"/></svg>(613) 555-0142</li>
    <li><svg><use href="#icon-mail"/></svg>paul@dunmoreroofing-example.com</li>
    <li><svg><use href="#icon-globe"/></svg>www.dunmoreroofing-example.com</li>
  </ul>
  <p class="address">4172 Township road 43, Millbrook Falls,ON K9X4T2</p>
  <p class="wordmark">Dunmore<br>Roofing</p>
</section>

<section class="card card--back">
  <div class="back__texture" role="img" aria-label="Faint dotted world map texture"></div>
  <p class="wordmark">Dunmore<br>Roofing</p>
  <p class="back__web">www.dunmoreroofing-example.com</p>
</section>

</body>
</html>
```